Website for "Bright Morrow Ltd" cleaning bsuiness

We require a website to expose our business to the local market. We want to provide background on who we are and what we do but in an easily digestible way. We clean domestic and commercial premises and want to provide a list of all of our services to potential customers. We operate out of Warrington in the UK.

We would like the website to be animated in some way so that the experience of using it is not dull or mundane. This website needs to be an extension of our company.

Target Market(s)

30 - 60 year olds for Domestic plus commercial clients

Industry/Entity Type

Cleaning Service

Coding

Coded - Design and coding required

Number of Pages Required

4 page

Font styles to use
Sans Serif

Colors
0455a3
3176b5
85acd3
cfdeed
ffffff
000000
1b1b1b
c8c8c8
757575

Requirements
Must have
• Logo which has been provided. Theme based around the logo and its colours. Simple layout to avoid confusion.
Nice to have
• Animations where possible to impress the customer.
Should not have
• any pictures of cleaning equipment, fairies, maids etc

```html
<!DOCTYPE html>
<html lang="en">
<head>
<meta charset="utf-8">
<title>Bright Morrow Ltd – Professional Cleaning Service</title>
<link href="https://fonts.googleapis.com/css2?family=Questrial&family=Open+Sans:ital,wght@0,400;0,600;1,400&display=swap" rel="stylesheet">
<style>
:root{
  --blue:#0455a3;
  --blue-mid:#3176b5;
  --blue-soft:#85acd3;
  --blue-pale:#cfdeed;
  --white:#ffffff;
  --black:#000000;
  --ink:#1b1b1b;
  --line:#c8c8c8;
  --grey:#757575;
  --panel:#eef1f5;
  --head:'Questrial', sans-serif;
  --body:'Open Sans', sans-serif;
}
*{margin:0;padding:0;box-sizing:border-box}
html,body{width:1200px;height:2875px;overflow:hidden;background:var(--white)}
body{position:relative;font-family:var(--body);color:var(--ink)}
.abs{position:absolute}
a{color:inherit;text-decoration:none}

/* header */
.site-header{position:absolute;left:0;top:0;width:1200px;height:163px;background:var(--white);border-bottom:1px solid #e3e3e3}
.contact-tab{position:absolute;top:0;height:38px;background:var(--blue);color:var(--white);font:11px var(--body);display:flex;align-items:center;justify-content:center;gap:8px;border-radius:0 0 24px 24px}
.contact-tab.phone{left:556px;width:249px}
.contact-tab.mail{left:828px;width:255px}
.brand{position:absolute;left:100px;top:56px;display:flex;align-items:center;gap:10px}
.brand-mark{width:36px;height:36px;border-radius:50%;background:var(--blue)}
.brand-name{font:700 24px var(--head);color:var(--blue);line-height:1.05;width:120px}
.main-nav{position:absolute;right:98px;top:88px;display:flex;gap:0;font:13px var(--head);color:var(--ink)}
.main-nav a{height:39px;line-height:39px;padding:0 17px}
.main-nav a.active{background:var(--blue);color:var(--white);padding:0 19px}

/* hero */
.hero{position:absolute;left:0;top:163px;width:1200px;height:537px;background:linear-gradient(100deg,#6f6a64 0%,#b9b4ad 25%,#e8e8e8 55%,#f4f4f4 75%,#d9dbdc 100%)}
.hero-title{position:absolute;left:159px;top:184px;width:387px;height:78px;background:rgba(4,85,163,.92);color:var(--white);font:38px var(--head);line-height:78px;padding-left:30px}
.hero-text{position:absolute;left:178px;top:262px;width:355px;height:83px;background:rgba(10,10,10,.8);color:var(--white);font:13px/24px var(--body);padding:16px 26px}
.hero-arrow{position:absolute;top:228px;width:62px;height:80px;background:rgba(140,140,140,.55);display:flex;align-items:center;justify-content:center}
.hero-arrow.prev{left:-18px;border-radius:0 40px 40px 0;padding-left:14px}
.hero-arrow.next{right:-18px;border-radius:40px 0 0 40px;padding-right:14px}

/* headings */
.section-title{font:28px var(--head);color:var(--ink);position:absolute}
.rule{position:absolute;height:4px;width:66px;background:var(--blue)}
.center{text-align:center;left:0;width:1200px}
.btn{position:absolute;font:12px var(--body);display:flex;align-items:center;justify-content:center}
.btn.solid{background:var(--blue);color:var(--white)}
.btn.ghost{border:2px solid var(--white);color:var(--white)}

/* welcome */
.welcome{position:absolute;left:0;top:700px;width:1200px;height:387px}
.welcome p{position:absolute;left:100px;width:460px;font:11.5px/21px var(--body);color:var(--grey)}
.service-card{position:absolute;top:51px;width:237px}
.service-card .photo{height:150px}
.service-card h3{font:15px var(--head);color:var(--blue);margin-top:28px}
.service-card p.desc{position:static;width:auto;font:11.5px/20px var(--body);color:var(--grey);margin-top:6px}
.service-card .more{display:block;font:11px var(--body);color:var(--blue);margin-top:5px}

/* who we are */
.who{position:absolute;left:0;top:1087px;width:1200px;height:318px;background:linear-gradient(180deg,#2c2c2c,#1a1a1a 60%,#262626)}
.who .section-title,.what .section-title{color:var(--white)}
.who p{position:absolute;left:200px;width:800px;text-align:center;color:var(--white);font:12px/25px var(--body)}

/* projects */
.projects{position:absolute;left:0;top:1405px;width:1200px;height:435px;background:var(--panel)}
.project-card{position:absolute;top:132px;width:237px;height:236px;background:var(--white);border:1px solid #dcdcdc;padding:9px}
.project-card .photo{height:157px}
.project-card h3{font:14px var(--head);text-align:center;color:var(--ink);margin-top:14px}
.project-card .date{font:600 10px var(--body);text-align:center;color:var(--blue);margin-top:6px}

/* what we do */
.what{position:absolute;left:0;top:1840px;width:1200px;height:505px;background:linear-gradient(120deg,#0a3f86 0%,#0b4a9a 45%,#1d5bab 70%,#0c3f82 100%)}
.offer{position:absolute;top:147px;width:330px;text-align:center;color:var(--white)}
.offer .icon{width:116px;height:116px;border-radius:50%;background:var(--white);margin:0 auto;display:flex;align-items:center;justify-content:center}
.offer h3{font:600 14px var(--body);margin-top:28px}
.offer p{font:11.5px/17px var(--body);margin:10px auto 0;width:300px}
.offer .btn{position:relative;margin:19px auto 0;width:124px;height:39px}

/* reviews */
.reviews{position:absolute;left:0;top:2345px;width:1200px;height:266px;background:var(--white)}
.quote-badge{position:absolute;left:165px;top:111px;width:94px;height:94px;border-radius:50%;background:var(--blue-mid);display:flex;align-items:center;justify-content:center}
.avatar{position:absolute;left:238px;top:110px;width:98px;height:98px;border-radius:50%;border:4px solid var(--white);background:linear-gradient(160deg,#d8c7b6,#9c8576)}
.review-text{position:absolute;left:370px;top:122px;width:670px;font:italic 12px/20px var(--body);color:var(--grey)}
.review-name{position:absolute;left:370px;top:200px;font:12px var(--body);color:var(--blue)}
.stars{color:#e8a92c;font-size:13px;letter-spacing:1px;margin-left:10px}
.slider-arrow{position:absolute;top:160px}

/* footer */
.site-footer{position:absolute;left:0;top:2611px;width:1200px;height:222px;background:var(--ink);color:#cfcfcf}
.foot-brand{position:absolute;left:100px;top:52px;display:flex;align-items:center;gap:10px}
.foot-brand .brand-mark{background:var(--white)}
.foot-brand .brand-name{color:var(--white)}
.social{position:absolute;left:100px;top:162px;display:flex;gap:7px}
.social span{width:23px;height:23px;border:1px solid #8a8a8a}
.divider{position:absolute;top:36px;width:1px;height:150px;background:#3a3a3a}
.foot-head{position:absolute;top:48px;font:15px var(--head);color:var(--white)}
.foot-list{position:absolute;top:82px;list-style:none;font:11px var(--body);color:#bdbdbd}
.foot-list li{height:22px}
.foot-list li::before{content:"›";margin-right:6px}
.newsletter{position:absolute;left:849px;top:80px;width:253px;height:33px;background:var(--white);color:#9a9a9a;font:10px var(--body);line-height:33px;padding-left:14px}
.submit{position:absolute;left:849px;top:119px;width:88px;height:32px;background:var(--blue);color:var(--white);font:600 12px var(--body);line-height:32px;text-align:center}
.copyright{position:absolute;left:0;top:2833px;width:1200px;height:42px;background:#0d0d0d;color:#bdbdbd;font:11px var(--body);line-height:42px;text-align:center}
</style>
</head>
<body>

<header class="site-header">
  <div class="contact-tab phone">
    <svg width="12" height="12" viewBox="0 0 24 24" fill="#fff"><path d="M6.6 10.8a15 15 0 0 0 6.6 6.6l2.2-2.2c.3-.3.7-.4 1-.2 1.1.4 2.3.6 3.6.6.6 0 1 .4 1 1V20c0 .6-.4 1-1 1A17 17 0 0 1 3 4c0-.6.4-1 1-1h3.5c.6 0 1 .4 1 1 0 1.3.2 2.5.6 3.6.1.3 0 .7-.2 1z"/></svg>
    Call Us Today : (+111) 555-0142
  </div>
  <div class="contact-tab mail">
    <svg width="12" height="10" viewBox="0 0 24 18" fill="#fff"><path d="M0 0h24v18H0z" fill="none"/><path d="M1 1h22v16H1z" stroke="#fff" stroke-width="2" fill="none"/><path d="M1 1l11 9 11-9" stroke="#fff" stroke-width="2" fill="none"/></svg>
    Mail : info@brightmorrow.com
  </div>
  <div class="brand"><span class="brand-mark"></span><span class="brand-name">Bright Morrow Ltd</span></div>
  <nav class="main-nav">
    <a class="active" href="#">Home</a><a href="#">About Us</a><a href="#">Services</a><a href="#">What we do</a><a href="#">Our Staffs</a><a href="#">Testimonials</a><a href="#">Blog</a><a href="#">Contact Us</a>
  </nav>
</header>

<section class="hero" role="img" aria-label="Photo of a couple relaxing on a white sofa in a bright, clean living room">
  <div class="hero-title">Cleaning Services</div>
  <div class="hero-text">Fresh, spotless homes and offices across Warrington, cleaned with care...</div>
  <div class="hero-arrow prev"><svg width="14" height="22" viewBox="0 0 14 22"><path d="M11 2L3 11l8 9" stroke="#fff" stroke-width="3" fill="none"/></svg></div>
  <div class="hero-arrow next"><svg width="14" height="22" viewBox="0 0 14 22"><path d="M3 2l8 9-8 9" stroke="#fff" stroke-width="3" fill="none"/></svg></div>
</section>

<section class="welcome">
  <h2 class="section-title" style="left:100px;top:48px">Welcome to Bright Morrow</h2>
  <div class="rule" style="left:100px;top:88px"></div>
  <p style="top:112px">Our local team keeps homes and workplaces across Warrington fresh and spotless, with trained staff, clear pricing and friendly service you can rely on every single visit to your door.</p>
  <p style="top:190px">From a weekly tidy to a full deep clean, we plan each job around your routine, bring our own supplies and leave every room looking bright and cared for...</p>
  <a class="btn solid" style="left:100px;top:289px;width:122px;height:38px" href="#">Learn More Info</a>

  <div class="service-card" style="left:606px">
    <div class="photo" role="img" aria-label="Photo of a tidy, sunlit bedroom" style="background:linear-gradient(160deg,#cfc6b8,#8d7c68 60%,#5e4e3f)"></div>
    <h3>Domestic Clean</h3>
    <p class="desc">Regular and one-off cleans for houses and flats, covering kitchens, bathrooms, floors and more...</p>
    <a class="more" href="#">Read More &gt;&gt;</a>
  </div>
  <div class="service-card" style="left:863px">
    <div class="photo" role="img" aria-label="Photo of glass office towers against a blue sky" style="background:linear-gradient(160deg,#a9c3e0,#4d76a6 55%,#1f3f66)"></div>
    <h3>Commercial Clean</h3>
    <p class="desc">Reliable cleaning for offices, shops and shared spaces, scheduled before or after your hours...</p>
    <a class="more" href="#">Read More &gt;&gt;</a>
  </div>
</section>

<section class="who" role="img" aria-label="Dark photo of a large open-plan interior with tall windows">
  <h2 class="section-title center" style="top:50px">Who we are</h2>
  <div class="rule" style="left:567px;top:90px"></div>
  <p style="top:129px">Bright Morrow is a family run cleaning company based in Warrington. We started with a handful of homes and now look after houses, offices and shops across the area, always with the same care, honesty and attention to detail that our first customers came to trust...</p>
  <a class="btn ghost" style="left:539px;top:220px;width:122px;height:39px" href="#">Learn More Info</a>
</section>

<section class="projects">
  <h2 class="section-title center" style="top:48px">Recent Projects</h2>
  <div class="rule" style="left:567px;top:88px"></div>
  <article class="project-card" style="left:100px">
    <div class="photo" role="img" aria-label="Photo of a bright living room with a staircase" style="background:linear-gradient(160deg,#efece7,#c9bfb2 60%,#7b6b5c)"></div>
    <h3>Riverside family home</h3><div class="date">23.OCTOBER.2016</div>
  </article>
  <article class="project-card" style="left:353px">
    <div class="photo" role="img" aria-label="Photo of a white modern kitchen" style="background:linear-gradient(160deg,#f4f4f2,#d9dcda 55%,#9aa3a4)"></div>
    <h3>Modern kitchen refresh</h3><div class="date">23.OCTOBER.2016</div>
  </article>
  <article class="project-card" style="left:608px">
    <div class="photo" role="img" aria-label="Photo of a glass office block at dusk" style="background:linear-gradient(170deg,#6f9ed4,#2f5b8f 55%,#3b4e5e)"></div>
    <h3>City office block</h3><div class="date">23.OCTOBER.2016</div>
  </article>
  <article class="project-card" style="left:863px">
    <div class="photo" role="img" aria-label="Photo of a polished hotel lobby" style="background:linear-gradient(160deg,#e6ddcf,#b9a88f 55%,#7a6a55)"></div>
    <h3>Hotel lobby clean</h3><div class="date">23.OCTOBER.2016</div>
  </article>
</section>

<section class="what" role="img" aria-label="Blue-tinted photo of a couple viewing a bright, empty interior">
  <h2 class="section-title center" style="top:60px">What we do</h2>
  <div class="rule" style="left:567px;top:100px"></div>
  <div class="offer" style="left:80px">
    <div class="icon"><svg width="56" height="56" viewBox="0 0 56 56" fill="#1b1b1b"><path d="M28 6L4 27h7v22h13V35h8v14h13V27h7z"/></svg></div>
    <h3>Domestic Cleaning</h3>
    <p>Weekly, fortnightly or one-off visits tailored to your home, with vetted staff and all supplies brought along...</p>
    <a class="btn ghost" href="#">Learn More Info</a>
  </div>
  <div class="offer" style="left:435px">
    <div class="icon"><svg width="56" height="56" viewBox="0 0 56 56" fill="#1b1b1b"><path d="M8 8h40l4 12H4z"/><path d="M4 22h48v4a6 6 0 0 1-12 0 6 6 0 0 1-12 0 6 6 0 0 1-12 0 6 6 0 0 1-12 0z"/><path d="M8 32h40v18H8zm6 4v14h10V36zm16 0v8h12v-8z" fill-rule="evenodd"/></svg></div>
    <h3>Shop &amp; Retail</h3>
    <p>Spotless floors, windows and counters for shops and showrooms, cleaned around your opening hours...</p>
    <a class="btn ghost" href="#">Learn More Info</a>
  </div>
  <div class="offer" style="left:790px">
    <div class="icon"><svg width="56" height="56" viewBox="0 0 56 56" fill="#1b1b1b"><path d="M6 50V18h16v32zm24 0V6h20v44zM10 22h3v4h-3zm5 0h3v4h-3zm-5 8h3v4h-3zm5 0h3v4h-3zm-5 8h3v4h-3zm5 0h3v4h-3z" fill-rule="evenodd"/><path d="M34 10h4v4h-4zm8 0h4v4h-4zm-8 8h4v4h-4zm8 0h4v4h-4zm-8 8h4v4h-4zm8 0h4v4h-4zm-8 8h4v4h-4zm8 0h4v4h-4z" fill="#fff"/><path d="M2 50h52v3H2z"/></svg></div>
    <h3>Office Cleaning</h3>
    <p>Desks, kitchens and washrooms kept tidy for your staff, with flexible early or late schedules...</p>
    <a class="btn ghost" href="#">Learn More Info</a>
  </div>
</section>

<section class="reviews">
  <h2 class="section-title center" style="top:44px">Customer Reviews</h2>
  <div class="rule" style="left:567px;top:84px"></div>
  <svg class="slider-arrow" style="left:98px" width="12" height="18" viewBox="0 0 12 18"><path d="M10 2L3 9l7 7" stroke="#9a9a9a" stroke-width="2.5" fill="none"/></svg>
  <svg class="slider-arrow" style="left:1090px" width="12" height="18" viewBox="0 0 12 18"><path d="M2 2l7 7-7 7" stroke="#9a9a9a" stroke-width="2.5" fill="none"/></svg>
  <div class="quote-badge"><svg width="38" height="30" viewBox="0 0 38 30" fill="#fff"><path d="M0 30V16C0 7 5 1 14 0v6c-4 1-6 4-6 9h6v15zm22 0V16c0-9 5-15 14-16v6c-4 1-6 4-6 9h6v15z"/></svg></div>
  <div class="avatar" role="img" aria-label="Portrait photo of the reviewing customer"></div>
  <p class="review-text">Bright Morrow have cleaned our home every week for two years now. The team is always on time, polite and thorough, and the house feels properly fresh every time they leave. I would happily recommend them to anyone in Warrington looking for a cleaner they can trust...</p>
  <div class="review-name">-Daniel Harlow <span class="stars">★★★★☆</span></div>
</section>

<footer class="site-footer">
  <div class="foot-brand"><span class="brand-mark"></span><span class="brand-name">Bright Morrow Ltd</span></div>
  <div class="social"><span></span><span></span><span></span><span></span></div>
  <div class="divider" style="left:311px"></div>
  <div class="divider" style="left:575px"></div>
  <div class="divider" style="left:744px"></div>
  <h4 class="foot-head" style="left:355px">Navigation</h4>
  <ul class="foot-list" style="left:355px"><li>Home</li><li>About Us</li><li>Services</li><li>What we do</li><li>Our Staffs</li></ul>
  <ul class="foot-list" style="left:447px"><li>Testimonials</li><li>Blog</li><li>Contact Us</li></ul>
  <h4 class="foot-head" style="left:631px">Information</h4>
  <ul class="foot-list" style="left:631px"><li>Terms &amp; Conditions</li><li>Privacy Policy</li><li>Site MAp</li><li>Disclaimer</li></ul>
  <h4 class="foot-head" style="left:849px">Contact US</h4>
  <div class="newsletter">Enter Your E-mail Address</div>
  <div class="submit">Submit</div>
</footer>
<div class="copyright">Copyrights © 2016 . Bright Morrow | Allrights Reserved.</div>

</body>
</html>
```